Communication and Marketing agency needs a new presentation card

We are a group of communication and marketing agencies specialized in companies that are in the logistics and industrial sector. The head agency is TELVANO Grupo and the group consists of 4 agencies: TELVANO Media, TELVANO Digital, TELVANO Research and DifundeEnPantalla. We hace 4 offices in Spain (Madrid, Barcelona, Valencia and Murcia). We are looking for a clean and attractive design that transmits our experience, brand presence in the market and knowledge to those who receive the card.It has to maintain the colors of the logo that is attached.
Target Market(s)
logistics and industrial sector
Marketing department
Contact Information for Business Card
Clean and attractive design

```html
<!DOCTYPE html>
<html lang="en">
<head>
<meta charset="utf-8">
<title>TELVANO Grupo – Business Card</title>
<link rel="stylesheet" href="https://fonts.googleapis.com/css2?family=Open+Sans:wght@400;600&family=Oswald:wght@500;600&display=swap">
<style>
  :root {
    --stage: #2c2c2c;
    --card: #222222;
    --card-edge: #1b1b1b;
    --map-tone: #2e2e2e;
    --red: #d23a38;
    --white: #f4f4f4;
    --text-soft: #d8d8d8;
  }
  * { box-sizing: border-box; margin: 0; padding: 0; }
  html, body { width: 1200px; height: 900px; overflow: hidden; }
  body {
    background: var(--stage);
    font-family: "Open Sans", Arial, sans-serif;
    position: relative;
  }
  .card {
    position: absolute;
    left: 230px;
    width: 740px;
    height: 420px;
    background: var(--card);
    box-shadow: 0 10px 30px rgba(0,0,0,0.45);
    overflow: hidden;
  }
  .card--cover { top: 25px; }
  .card--contact { top: 455px; border-bottom: 5px solid var(--red); }

  .world-map-area {
    position: absolute;
    inset: 40px 30px 40px 30px;
    background: radial-gradient(ellipse at center, var(--map-tone) 0%, var(--card) 75%);
  }

  .brand-name {
    font-family: "Oswald", Arial, sans-serif;
    font-weight: 500;
    color: var(--red);
    letter-spacing: 2px;
    white-space: nowrap;
  }
  .card--cover .brand-name {
    position: absolute;
    left: 0; right: 0;
    top: 165px;
    text-align: center;
    font-size: 60px;
    line-height: 1;
  }
  .card--contact .brand-name {
    position: absolute;
    left: 55px;
    top: 110px;
    font-size: 44px;
    line-height: 1;
  }

  .divider {
    position: absolute;
    left: 385px;
    top: 95px;
    width: 3px;
    height: 170px;
    background: var(--red);
  }

  .person {
    position: absolute;
    left: 420px;
    top: 92px;
  }
  .person__name {
    font-family: "Oswald", Arial, sans-serif;
    font-weight: 600;
    font-size: 46px;
    line-height: 1;
    color: var(--white);
    letter-spacing: 2px;
  }
  .person__role {
    font-weight: 600;
    font-size: 19px;
    color: var(--red);
    letter-spacing: 1px;
    margin-top: 4px;
  }
  .contact-list { list-style: none; margin-top: 10px; }
  .contact-list li {
    display: flex;
    align-items: center;
    gap: 12px;
    font-size: 18px;
    color: var(--text-soft);
    line-height: 30px;
  }
  .contact-list svg { width: 16px; height: 16px; flex: none; }
  .highlight { color: var(--red); }

  .address {
    position: absolute;
    left: 0; right: 0;
    bottom: 32px;
    text-align: center;
    font-size: 17px;
    color: var(--text-soft);
  }
  .address__label { color: var(--red); }
</style>
</head>
<body>
  <section class="card card--cover">
    <div class="world-map-area" role="img" aria-label="Faint dotted world map in the background"></div>
    <div class="brand-name">TELVANO Grupo</div>
  </section>

  <section class="card card--contact">
    <div class="brand-name">TELVANO Grupo</div>
    <div class="divider"></div>
    <div class="person">
      <h1 class="person__name">MARTÍN SALAS</h1>
      <p class="person__role">CEO &amp; FOUNDER</p>
      <ul class="contact-list">
        <li>
          <svg viewBox="0 0 16 16" aria-hidden="true"><rect x="4" y="1" width="8" height="14" rx="1.5" fill="none" stroke="#d23a38" stroke-width="1.6"/><circle cx="8" cy="12.3" r="0.9" fill="#d23a38"/></svg>
          000 111 222 3333
        </li>
        <li>
          <svg viewBox="0 0 16 16" aria-hidden="true"><rect x="1" y="3" width="14" height="10" rx="1" fill="#d23a38"/><path d="M1.5 3.5 L8 9 L14.5 3.5" fill="none" stroke="#222" stroke-width="1.3"/></svg>
          urname@email.com
        </li>
        <li>
          <svg viewBox="0 0 16 16" aria-hidden="true"><circle cx="9.5" cy="6.5" r="4.5" fill="none" stroke="#d23a38" stroke-width="1.8"/><line x1="6.3" y1="9.7" x2="1.5" y2="14.5" stroke="#d23a38" stroke-width="2"/></svg>
          <span>www.<span class="highlight">ursitename</span>.com</span>
        </li>
      </ul>
    </div>
    <p class="address"><span class="address__label">Address :</span> Your Street Address, NewYork City 1234</p>
  </section>
</body>
</html>
```